Dultavo.com webside

I want to build a Dultavo.com retail website use on Shopify, reselling three main categories: Office Supplies, Packing Supplies, and Home Consumables. I also wish the webpage has the same functions as the Zelvik home page. The page is split into three different parts with the top being a sliding screen showcasing promotion products, below it being the three categories, and finally, a moving screen showing company missions.
Target Market(s)
U.S online
Industry/Entity Type
Office Supplies, packing Supplies and Home Consumables
Coding
Coded - Design and coding required
Number of Pages Required
5+ page
Look and feel

```html
<!DOCTYPE html>
<html lang="en">
<head>
<meta charset="utf-8">
<title>Dultavo — Office, Packing &amp; Home Supplies</title>
<link rel="stylesheet" href="https://fonts.googleapis.com/css2?family=Raleway:ital,wght@0,400;0,500;0,600;0,700;1,500&display=swap">
<style>
:root{
  --teal:#1cb497;
  --teal-dark:#10a68b;
  --teal-light:#6cd8c7;
  --heading:#17a88d;
  --hero-a:#3d9a98;
  --hero-b:#1d7174;
  --wood-a:#e9c48d;
  --wood-b:#c9955a;
  --mint:#e9f8f5;
  --ink:#222;
  --white:#fff;
  --black:#000;
}
*{margin:0;padding:0;box-sizing:border-box}
html,body{width:1200px;height:3380px;overflow:hidden}
body{font-family:"Raleway",sans-serif;color:var(--ink);background:var(--white);position:relative}
.abs{position:absolute}
.announce{left:0;top:0;width:1200px;height:40px;background:var(--teal-light);color:var(--white);font-size:13px;display:flex;align-items:center;justify-content:center;gap:30px}
.navbar{left:0;top:40px;width:1200px;height:69px;background:var(--teal)}
.brand{left:98px;top:14px;font-size:37px;font-weight:700;color:var(--white)}
.nav-link{top:24px;font-size:15px;color:var(--white)}
.search-label{left:1004px;top:26px;font-size:15px;font-style:italic;color:var(--white)}
.hero{left:0;top:109px;width:1200px;height:573px;background:radial-gradient(ellipse at 40% 40%,var(--hero-a),var(--hero-b))}
.wood{left:0;top:498px;width:1200px;height:75px;background:linear-gradient(var(--wood-a),var(--wood-b))}
.hero-art{left:10px;top:140px;width:400px;height:420px;border-radius:40px;background:radial-gradient(circle,#f0c84a 0%,#e65a6a 45%,rgba(61,154,152,0) 72%)}
.welcome{left:606px;top:135px;font-size:50px;font-weight:500;color:var(--white)}
.hero-name{left:604px;top:195px;font-size:112px;font-weight:700;color:var(--white);letter-spacing:2px}
.cashback{left:622px;top:345px;font-size:40px;font-weight:700;color:var(--white)}
.btn-solid{background:var(--teal);color:var(--white);display:flex;align-items:center;justify-content:center;font-weight:600}
.section-title{left:0;width:1200px;text-align:center;font-size:40px;font-weight:700;color:var(--heading)}
.photo{position:absolute}
.cat-label{font-size:28px;color:var(--ink)}
.about-panel{left:47px;top:1448px;width:621px;height:447px;background:var(--mint);border:1px dashed #bfe8e0}
.about-title{left:98px;top:1498px;font-size:45px;font-weight:700;color:var(--heading)}
.about-text{left:101px;top:1583px;width:450px;font-size:17px;line-height:26px;color:#333}
.prod-name{font-size:27px}
.prod-price{font-size:21px}
.btn-outline{width:134px;height:43px;border:2px solid #1b2a3a;display:flex;align-items:center;justify-content:center;font-size:19px}
.promo{left:0;top:2657px;width:1200px;height:343px;background:linear-gradient(90deg,#74dccb,#5fd3c0 50%,#72dbca)}
.promo-title{left:0;top:2718px;width:1200px;text-align:center;font-size:40px;font-weight:500;color:var(--white)}
.promo-text{left:170px;top:2790px;width:860px;text-align:center;font-size:15px;line-height:26px;color:var(--white)}
.footer{left:0;top:3000px;width:1200px;height:380px;background:var(--black);color:var(--white)}
.f-head{font-size:30px;font-weight:700}
.f-links{font-size:17px;line-height:25.6px;list-style:none}
.f-text{font-size:15px;line-height:26px}
.social{display:flex;gap:12px}
.social span{width:10px;height:10px;border-radius:50%;background:#2a86d8;display:block}
</style>
</head>
<body>

<div class="abs announce"><span>&#8249;</span><span>I have a podcast that will be launching soon.</span><span>&#8250;</span></div>

<header class="abs navbar">
  <div class="abs brand">Dultavo</div>
  <span class="abs nav-link" style="left:279px">Home</span>
  <span class="abs nav-link" style="left:358px">About Me</span>
  <span class="abs nav-link" style="left:463px">Office Supplies</span>
  <span class="abs nav-link" style="left:605px">Product</span>
  <span class="abs nav-link" style="left:696px">Packing Supplies</span>
  <span class="abs nav-link" style="left:855px">Contact us</span>
  <svg class="abs" style="left:962px;top:24px" width="22" height="22" viewBox="0 0 22 22"><circle cx="9" cy="9" r="6.5" fill="none" stroke="#fff" stroke-width="3"/><line x1="14" y1="14" x2="20" y2="20" stroke="#fff" stroke-width="3.5" stroke-linecap="round"/></svg>
  <span class="search-label">Search</span>
  <svg class="abs" style="left:1079px;top:25px" width="22" height="20" viewBox="0 0 22 20"><path d="M1 2h4l3 11h10l3-8H7" fill="none" stroke="#fff" stroke-width="2.5"/><circle cx="9" cy="17" r="2" fill="#fff"/><circle cx="17" cy="17" r="2" fill="#fff"/></svg>
</header>

<section class="abs hero">
  <div class="abs wood"></div>
  <div class="abs hero-art" role="img" aria-label="Shopping cart filled with stationery and office supplies"></div>
  <div class="abs welcome">Welcome To</div>
  <div class="abs hero-name">DULTAVO</div>
  <div class="abs cashback">UP TO &nbsp;75 % Cashback</div>
  <div class="abs btn-solid" style="left:618px;top:431px;width:166px;height:50px;font-size:22px">Get started</div>
</section>

<h2 class="abs section-title" style="top:750px">Our &nbsp;Categories</h2>
<div class="photo" style="left:98px;top:881px;width:323px;height:408px;background:linear-gradient(100deg,#5a9a3a,#9ad43a 40%,#e88a4a 75%,#f0c0a0)" role="img" aria-label="Hand picking a green binder from an office shelf"></div>
<div class="photo" style="left:442px;top:881px;width:323px;height:408px;background:linear-gradient(160deg,#e8a060,#f2ece6 45%,#b89070 80%,#3a3028)" role="img" aria-label="Tape dispenser sealing a cardboard box"></div>
<div class="photo" style="left:778px;top:881px;width:322px;height:408px;background:linear-gradient(180deg,#d8d8dc,#6a7080 35%,#4a4a50 65%,#c05a30)" role="img" aria-label="Store aisle stocked with home consumables"></div>
<div class="abs cat-label" style="left:98px;top:1308px">Office Supplies</div>
<div class="abs cat-label" style="left:442px;top:1308px">Packing Supplies</div>
<div class="abs cat-label" style="left:778px;top:1308px">Home Consumables</div>

<section>
  <div class="abs about-panel"></div>
  <h2 class="abs about-title">About Us</h2>
  <p class="abs about-text">Lorem ipsum dolor sit amet, consectetur adipiscing elit, sed do eiusmod tempor incididunt ut labore et dolore magna aliqua. Ut enim ad minim veniam, quis nostrud exercitation ullamco laboris nisi ut aliquip ex ea commodo consequat Lorem ipsum dolor sit amet, consectetur adipiscing elit, sed do eiusmod tempor</p>
  <div class="abs btn-solid" style="left:98px;top:1772px;width:162px;height:54px;font-size:22px">Read More</div>
  <div class="photo" style="left:668px;top:1448px;width:470px;height:497px;background:linear-gradient(170deg,#eef0f2,#cfd4d8 50%,#9aa0a6 75%,#e6e8ea)" role="img" aria-label="Bright modern open-plan office with desks and computers"></div>
</section>

<h2 class="abs section-title" style="top:2008px">Our Product</h2>
<div class="photo" style="left:98px;top:2130px;width:236px;height:295px;background:linear-gradient(100deg,#9ad43a,#b8e060 35%,#f2e0d0 55%,#e86a4a)" role="img" aria-label="Green folders on an office shelf"></div>
<div class="photo" style="left:363px;top:2130px;width:236px;height:295px;background:linear-gradient(150deg,#f4f4f4,#c8c8c8 45%,#e8d050 65%,#e0e0e0)" role="img" aria-label="Spiral notebook with pens"></div>
<div class="photo" style="left:614px;top:2130px;width:236px;height:295px;background:linear-gradient(180deg,#f0f0f0,#c0c8cc 45%,#e06a9a 70%,#40b0c8)" role="img" aria-label="Cleaning bottles, gloves and sponges in a basket"></div>
<div class="photo" style="left:864px;top:2130px;width:235px;height:295px;background:linear-gradient(150deg,#3a4a60,#e8806a 30%,#202020 60%,#60a8e0)" role="img" aria-label="Hands installing a printer toner cartridge"></div>

<div class="abs prod-name" style="left:115px;top:2432px">Office</div>
<div class="abs prod-price" style="left:115px;top:2472px">$250.00</div>
<div class="abs btn-outline" style="left:117px;top:2525px">Buy Now</div>
<div class="abs prod-name" style="left:380px;top:2432px">Packing</div>
<div class="abs prod-price" style="left:380px;top:2472px">$220.00</div>
<div class="abs btn-outline" style="left:382px;top:2525px">Buy Now</div>
<div class="abs prod-name" style="left:630px;top:2432px">Home</div>
<div class="abs prod-price" style="left:630px;top:2472px">$150.00</div>
<div class="abs btn-outline" style="left:632px;top:2525px">Buy Now</div>
<div class="abs prod-name" style="left:880px;top:2432px">Consumables</div>
<div class="abs prod-price" style="left:880px;top:2472px">$125.00</div>
<div class="abs btn-outline" style="left:882px;top:2525px">Buy Now</div>

<section class="abs promo" role="img" aria-label="Soft teal backdrop of promotional cleaning products"></section>
<h2 class="abs promo-title">Showcasing Promotional Products</h2>
<p class="abs promo-text">Lorem ipsum dolor sit amet, consectetur adipiscing elit, sed do eiusmod tempor incididunt ut labore et dolore magna aliqua. Ut enim ad minim veniam, quis nostrud exercitation ullamco laboris nisi ut aliquip ex ea commodo consequat. Duis aute irure dolor in reprehenderit in voluptate velit esse cillum dolore eu fugiat nulla pariatur.</p>
<div class="abs btn-solid" style="left:522px;top:2917px;width:153px;height:47px;font-size:15px;font-weight:500;gap:16px;background:var(--teal-dark)">Learn More <span>&#10230;</span></div>

<footer class="abs footer">
  <div class="abs f-head" style="left:100px;top:50px">Info</div>
  <ul class="abs f-links" style="left:99px;top:100px">
    <li>Home</li><li>About Me</li><li>Office Supplies</li><li>Product</li><li>Packing Supplies</li><li>Contact us</li>
  </ul>
  <div class="abs f-head" style="left:331px;top:50px">Thank you</div>
  <p class="abs f-text" style="left:332px;top:100px;width:300px">Lorem ipsum dolor sit amet, consectetur adipiscing elit, sed do eiusmod tempor incididunt ut labore et dolore magna aliqua. Ut enim ad minim veniam</p>
  <div class="abs social" style="left:333px;top:236px"><span></span><span></span><span style="background:#d04a3a"></span><span></span></div>
  <div class="abs f-head" style="left:690px;top:50px">Sign up and save</div>
  <p class="abs" style="left:692px;top:100px;width:400px;font-size:18px;line-height:26px">"Lorem ipsum dolor sit amet, consectetur &nbsp;elit, sed do eiusmod tempor incididunt</p>
  <div class="abs" style="left:707px;top:180px;font-size:15px;font-style:italic">hello@dultavomail.com</div>
  <div class="abs btn-solid" style="left:695px;top:231px;width:122px;height:46px;font-size:16px;font-style:italic;font-weight:700">Subscribe</div>
  <div class="abs" style="left:109px;top:312px;font-size:17px;font-weight:500">© copyrights 2022 &nbsp;Dultavo | &nbsp;All Rights Reserved</div>
</footer>

</body>
</html>
```